Quran Jar

So I need help designing bespoke jars which will contain religious quotes.

So there will be three jars in total sold either individually or in two or as a three.

Each Jar will have different contents and preferably a different colour scheme.

I want the packaging to be customised with my branding and logo and to make the product stand out I am thinking of packing it further in a cotton bag with my branding.

```html
<!DOCTYPE html>
<html lang="en">
<head>
<meta charset="utf-8">
<title>Still Waters – Jar Labels</title>
<link rel="stylesheet" href="https://fonts.googleapis.com/css2?family=Lato:wght@300;400&family=Montserrat:wght@500&family=Quicksand:wght@600&display=swap">
<style>
  :root {
    --stage: #e6e6e8;
    --green: #294c38;
    --green-band: #1d3628;
    --gold: #7f6219;
    --gold-band: #5a4510;
    --paper: #ffffff;
    --paper-band: #d3d3d3;
    --brand-light: #dcbc6c;
    --brand-dark: #7f6219;
    --title-light: #ffffff;
    --title-dark: #2a2a2a;
    --c-happiness: #f9dc1e;
    --c-sadness: #8ecdf7;
    --c-anxiety: #a455e0;
    --c-gratefulness: #86e57d;
    --c-patience: #fba000;
    --c-hope: #f9c9d8;
    --c-forgiveness: #ffffff;
    --c-love: #f40d0d;
  }
  * { margin: 0; padding: 0; box-sizing: border-box; }
  html, body { width: 1200px; height: 340px; overflow: hidden; }
  body {
    background: linear-gradient(180deg, #ffffff 0%, #e9e9eb 55%, #b9b9bd 100%);
    position: relative;
  }
  .label-set { position: absolute; top: 57px; left: 71px; display: flex; gap: 23px; }
  .jar-label {
    position: relative; width: 337px; height: 226px; overflow: hidden;
    text-align: center;
  }
  .jar-label--quran { background: var(--green); --band: var(--green-band); --brand: var(--brand-light); --title: var(--title-light); --body: #e6ece8; --faint: rgba(255,255,255,.12); }
  .jar-label--hadith { background: var(--gold); --band: var(--gold-band); --brand: var(--brand-light); --title: var(--title-light); --body: #f3ead2; --faint: rgba(255,255,255,.12); }
  .jar-label--dua { background: var(--paper); --band: var(--paper-band); --brand: var(--brand-dark); --title: var(--title-dark); --body: #555; --label-ink: #3a3a3a; --faint: rgba(0,0,0,.05); }

  .brand-mark {
    position: absolute; top: 70px; left: 50%; transform: translateX(-50%);
    width: 20px; height: 20px; border-radius: 50%; background: var(--brand);
  }
  .brand-name {
    position: absolute; top: 98px; left: 0; right: 0;
    font: 600 14px/1 "Quicksand", sans-serif; color: var(--brand);
  }
  .brand-tagline {
    position: absolute; top: 116px; left: 0; right: 0;
    font: 400 2.6px/1 "Lato", sans-serif; letter-spacing: 1.4px;
    text-transform: uppercase; color: var(--brand);
  }
  .jar-title {
    position: absolute; top: 124px; left: 0; right: 0;
    font: 300 27px/1 "Lato", sans-serif; color: var(--title); letter-spacing: .5px;
  }
  .jar-word {
    position: absolute; top: 147px; left: 0; right: 0;
    font: 300 16px/1 "Lato", sans-serif; color: var(--title);
  }
  .mood-bar {
    position: absolute; top: 178px; left: 13px; width: 311px; height: 15px;
    display: flex; border-radius: 7px; overflow: hidden; background: var(--band);
  }
  .mood {
    flex: 1; display: flex; flex-direction: column;
    border-right: 0.6px solid rgba(255,255,255,.6);
  }
  .mood:last-child { border-right: 0; }
  .mood__swatch { height: 6px; }
  .mood__name {
    flex: 1; display: flex; align-items: center; justify-content: center;
    font: 500 4.2px/1 "Montserrat", sans-serif; color: var(--label-ink, #ffffff);
  }
  .jar-blurb {
    position: absolute; top: 197px; left: 40px; right: 40px;
    font: 400 3.7px/1.3 "Montserrat", sans-serif; color: var(--body);
  }
  .jar-pill { position: absolute; top: 209px; left: 104px; width: 25px; height: 4px; border-radius: 2px; background: var(--faint); }
  .jar-foot { position: absolute; top: 221px; left: 131px; right: 0; height: 5px; border-radius: 3px 0 0 3px; background: var(--faint); }
</style>
</head>
<body>
<main class="label-set">
  <section class="jar-label jar-label--quran">
    <span class="brand-mark"></span>
    <p class="brand-name">Still Waters</p>
    <p class="brand-tagline">Calm words for every day</p>
    <h1 class="jar-title">QURAN</h1>
    <p class="jar-word">JAR</p>
    <div class="mood-bar">
      <div class="mood"><span class="mood__swatch" style="background:var(--c-happiness)"></span><span class="mood__name">HAPPINESS</span></div>
      <div class="mood"><span class="mood__swatch" style="background:var(--c-sadness)"></span><span class="mood__name">SADNESS</span></div>
      <div class="mood"><span class="mood__swatch" style="background:var(--c-anxiety)"></span><span class="mood__name">ANXIETY</span></div>
      <div class="mood"><span class="mood__swatch" style="background:var(--c-gratefulness)"></span><span class="mood__name">GRATEFULNESS</span></div>
      <div class="mood"><span class="mood__swatch" style="background:var(--c-patience)"></span><span class="mood__name">PATIENCE</span></div>
      <div class="mood"><span class="mood__swatch" style="background:var(--c-hope)"></span><span class="mood__name">HOPE</span></div>
      <div class="mood"><span class="mood__swatch" style="background:var(--c-forgiveness)"></span><span class="mood__name">FORGIVENESS</span></div>
      <div class="mood"><span class="mood__swatch" style="background:var(--c-love)"></span><span class="mood__name">LOVE</span></div>
    </div>
    <p class="jar-blurb">Lorem ipsum dolor sit amet, consectetur adipiscing elit, sed do eiusmod tempor incididunt ut labore et dolore magna aliqua. Ut enim ad minim veniam, quis nostrud exercitation ullamco laboris nisi ut aliquip ex ea commodo consequat.</p>
    <span class="jar-pill"></span>
    <span class="jar-foot"></span>
  </section>

  <section class="jar-label jar-label--hadith">
    <span class="brand-mark"></span>
    <p class="brand-name">Still Waters</p>
    <p class="brand-tagline">Calm words for every day</p>
    <h1 class="jar-title">HADITH</h1>
    <p class="jar-word">JAR</p>
    <div class="mood-bar">
      <div class="mood"><span class="mood__swatch" style="background:var(--c-happiness)"></span><span class="mood__name">HAPPINESS</span></div>
      <div class="mood"><span class="mood__swatch" style="background:var(--c-sadness)"></span><span class="mood__name">SADNESS</span></div>
      <div class="mood"><span class="mood__swatch" style="background:var(--c-anxiety)"></span><span class="mood__name">ANXIETY</span></div>
      <div class="mood"><span class="mood__swatch" style="background:var(--c-gratefulness)"></span><span class="mood__name">GRATEFULNESS</span></div>
      <div class="mood"><span class="mood__swatch" style="background:var(--c-patience)"></span><span class="mood__name">PATIENCE</span></div>
      <div class="mood"><span class="mood__swatch" style="background:var(--c-hope)"></span><span class="mood__name">HOPE</span></div>
      <div class="mood"><span class="mood__swatch" style="background:var(--c-forgiveness)"></span><span class="mood__name">FORGIVENESS</span></div>
      <div class="mood"><span class="mood__swatch" style="background:var(--c-love)"></span><span class="mood__name">LOVE</span></div>
    </div>
    <p class="jar-blurb">Lorem ipsum dolor sit amet, consectetur adipiscing elit, sed do eiusmod tempor incididunt ut labore et dolore magna aliqua. Ut enim ad minim veniam, quis nostrud exercitation ullamco laboris nisi ut aliquip ex ea commodo consequat.</p>
    <span class="jar-pill"></span>
    <span class="jar-foot"></span>
  </section>

  <section class="jar-label jar-label--dua">
    <span class="brand-mark"></span>
    <p class="brand-name">Still Waters</p>
    <p class="brand-tagline">Calm words for every day</p>
    <h1 class="jar-title">DUA</h1>
    <p class="jar-word">JAR</p>
    <div class="mood-bar">
      <div class="mood"><span class="mood__swatch" style="background:var(--c-happiness)"></span><span class="mood__name">HAPPINESS</span></div>
      <div class="mood"><span class="mood__swatch" style="background:var(--c-sadness)"></span><span class="mood__name">SADNESS</span></div>
      <div class="mood"><span class="mood__swatch" style="background:var(--c-anxiety)"></span><span class="mood__name">ANXIETY</span></div>
      <div class="mood"><span class="mood__swatch" style="background:var(--c-gratefulness)"></span><span class="mood__name">GRATEFULNESS</span></div>
      <div class="mood"><span class="mood__swatch" style="background:var(--c-patience)"></span><span class="mood__name">PATIENCE</span></div>
      <div class="mood"><span class="mood__swatch" style="background:var(--c-hope)"></span><span class="mood__name">HOPE</span></div>
      <div class="mood"><span class="mood__swatch" style="background:#f2f2f2"></span><span class="mood__name">FORGIVENESS</span></div>
      <div class="mood"><span class="mood__swatch" style="background:var(--c-love)"></span><span class="mood__name">LOVE</span></div>
    </div>
    <p class="jar-blurb">Lorem ipsum dolor sit amet, consectetur adipiscing elit, sed do eiusmod tempor incididunt ut labore et dolore magna aliqua. Ut enim ad minim veniam, quis nostrud exercitation ullamco laboris nisi ut aliquip ex ea commodo consequat.</p>
    <span class="jar-pill"></span>
    <span class="jar-foot"></span>
  </section>
</main>
</body>
</html>
```